Create modern and sleek business card for luxury real estate company

We're a "boutique" real estate office looking for a design that gets across a highly modern luxury brand. Blacks and whites are probably the best colors unless we try a silver foil for the logo. I've attached a version of our current logo here. I'd like to swap out the current font on there with Gotham Light Regular.

I'm looking to have one side of the card have the logo with the space for our agents info on the other side.

Target Market(s)

Young professionals in a "luxury" headspace

Industry/Entity Type

Real estate

Contact Information for Business Card

A place for agent name, cell number, website. The slogan "Quietly Elevating Every Address".

Font styles to use
Other font styles liked:
• Gotham Regular

Colors

Designer to choose only greyscale colors for use in the design.

Requirements
Must have
• Matte black as the background color. Clean lines and use of contrast. A specific design aspect that will use silver foil.
Nice to have
• Up in the air on integrating a QR code
Should not have
• Any houses or other real estate related design (ex: a clip art house)

```html
<!DOCTYPE html>
<html lang="en">
<head>
<meta charset="utf-8">
<title>Meridian Realty – Business Card</title>
<link href="https://fonts.googleapis.com/css2?family=Open+Sans:wght@400;700&display=swap" rel="stylesheet">
<style>
  :root {
    --backdrop: #3a3a3a;
    --card-black: #0b0b0b;
    --ink-white: #f4f4f4;
    --ink-grey: #8a8a8a;
    --rule-grey: #5c5c5c;
    --gloss-dark: #1c1c1c;
    --gloss-mid: #4a4a4a;
    --silver: #c9c9c9;
  }
  * { margin: 0; padding: 0; box-sizing: border-box; }
  html, body {
    width: 1200px; height: 801px; overflow: hidden;
    background: var(--backdrop);
    font-family: "Open Sans", sans-serif;
  }
  .stage {
    position: relative; width: 1200px; height: 801px;
    display: flex; align-items: center; justify-content: center; gap: 60px;
  }
  .card {
    position: relative; width: 500px; height: 286px;
    background: var(--card-black);
    box-shadow: 0 14px 30px rgba(0,0,0,0.45);
    overflow: hidden;
  }

  /* Front: agent details */
  .brand {
    position: absolute; left: 34px; top: 92px;
    display: flex; align-items: center; gap: 12px;
  }
  .brand-circle {
    width: 44px; height: 44px; border-radius: 50%;
    border: 2px solid var(--ink-white);
  }
  .brand-name {
    color: var(--ink-white); font-size: 19px; font-weight: 400;
    letter-spacing: 2px; line-height: 1.15; text-transform: uppercase;
  }
  .agent {
    position: absolute; right: 34px; top: 36px; text-align: right;
  }
  .agent-name {
    color: var(--ink-white); font-weight: 700; font-size: 17px; letter-spacing: 0.5px;
  }
  .agent-title { color: var(--ink-grey); font-size: 11px; margin-top: 2px; }
  .rule {
    position: absolute; left: 34px; right: 34px; top: 162px;
    height: 1px; background: var(--rule-grey);
  }
  .contacts {
    position: absolute; left: 34px; top: 186px;
    list-style: none; color: var(--ink-white); font-size: 11.5px;
  }
  .contacts li { display: flex; align-items: center; gap: 8px; height: 20px; }
  .contacts svg { width: 11px; height: 11px; flex: none; }
  .slogan {
    position: absolute; right: 34px; top: 180px;
    color: var(--ink-white); font-size: 11.5px;
  }

  /* Back: foil mark */
  .back-mark {
    position: absolute; left: -50px; top: 10px; width: 270px; height: 270px;
  }
  .back-brand {
    position: absolute; right: 40px; top: 108px;
    color: var(--silver); font-size: 28px; font-weight: 400;
    letter-spacing: 3px; line-height: 1.1; text-transform: uppercase;
  }
</style>
</head>
<body>
<main class="stage">

  <section class="card card-front" aria-label="Card front">
    <div class="agent">
      <p class="agent-name">DANIEL HARTWELL</p>
      <p class="agent-title">President</p>
    </div>

    <div class="brand">
      <span class="brand-circle"></span>
      <span class="brand-name">Meridian<br>Realty</span>
    </div>

    <div class="rule"></div>

    <ul class="contacts">
      <li>
        <svg viewBox="0 0 12 12"><circle cx="6" cy="6" r="6" fill="var(--ink-white)"/><path d="M4 3.2l1 1.3-.6.7a4 4 0 0 0 2.4 2.4l.7-.6 1.3 1-.7 1A5 5 0 0 1 3 4z" fill="var(--card-black)"/></svg>
        555-310-4827
      </li>
      <li>
        <svg viewBox="0 0 12 12"><circle cx="6" cy="6" r="6" fill="var(--ink-white)"/><rect x="3" y="4" width="6" height="4.2" fill="var(--card-black)"/><path d="M3 4l3 2.3L9 4" stroke="var(--ink-white)" stroke-width=".7" fill="none"/></svg>
        dhartwell@meridianrealty.com
      </li>
      <li>
        <svg viewBox="0 0 12 12"><circle cx="6" cy="6" r="6" fill="var(--ink-white)"/><circle cx="6" cy="6" r="3.2" fill="none" stroke="var(--card-black)" stroke-width=".8"/><path d="M2.8 6h6.4M6 2.8v6.4" stroke="var(--card-black)" stroke-width=".7"/></svg>
        www.meridianrealty.com
      </li>
    </ul>

    <p class="slogan">Quietly Elevating Every Address</p>
  </section>

  <section class="card card-back" aria-label="Card back">
    <svg class="back-mark" viewBox="0 0 270 270" aria-hidden="true">
      <defs>
        <linearGradient id="gloss" x1="0" y1="0" x2="1" y2="1">
          <stop offset="0" stop-color="var(--gloss-dark)"/>
          <stop offset="0.6" stop-color="var(--gloss-mid)"/>
          <stop offset="1" stop-color="var(--gloss-dark)"/>
        </linearGradient>
      </defs>
      <circle cx="135" cy="135" r="122" fill="none" stroke="url(#gloss)" stroke-width="6"/>
    </svg>
    <p class="back-brand">Meridian<br>Realty</p>
  </section>

</main>
</body>
</html>
```